Marlow Vale Stud website

We would like to create a horse stud/agistment farm website similar to this websites we have attached below:
www.thornbeck.com.au
www.quillstead.com.au
www.brackley.com
www.pimsey.com.au
The main colour scheme are purple and white to align with the stable's racing colours.
We have also attach the company logo and also images of the farm and create some ideas for the website.
Many thanks for looking into this project!

```html
<!DOCTYPE html>
<html lang="en">
<head>
<meta charset="utf-8">
<title>Marlow Vale Stud</title>
<link rel="stylesheet" href="https://fonts.googleapis.com/css2?family=Varela+Round&family=Lato:wght@400;700&family=Lora&display=swap">
<style>
  :root {
    --purple: #341338;
    --purple-deep: #2e0f33;
    --white: #ffffff;
    --ink: #111111;
    --black: #000000;
    --grass: #4f7a2c;
  }
  * { box-sizing: border-box; margin: 0; padding: 0; }
  html, body { width: 1200px; height: 2432px; overflow: hidden; background: var(--white); }
  body { position: relative; font-family: "Varela Round", sans-serif; color: var(--ink); }
  .abs { position: absolute; }
  .center-x { left: 0; width: 1200px; text-align: center; }

  /* Hero */
  .hero {
    left: 0; top: 0; width: 1200px; height: 683px;
    background:
      linear-gradient(180deg, #4e5a72 0%, #7d8aa3 18%, #c9b8a0 30%, #e8c48c 36%, #6b7a86 44%, #3f4a3a 52%, #2f4a22 62%, #4b7a2a 78%, #3e6422 100%);
  }
  .hero-tree {
    left: 0; top: 0; width: 230px; height: 683px;
    background: linear-gradient(90deg, rgba(150,110,40,0.55), rgba(150,110,40,0));
  }
  .brand {
    left: 138px; top: 52px; color: var(--white);
    font-size: 22px; line-height: 1;
  }
  .nav { top: 0; left: 0; }
  .nav-item {
    position: absolute; top: 60px; font-size: 14px; color: var(--white);
    transform: translateX(-50%); white-space: nowrap;
  }
  .nav-active {
    left: 503px; top: 0; width: 73px; height: 94px; background: var(--purple);
  }
  .hero-title {
    top: 253px; font-size: 53px; color: var(--white); letter-spacing: 1px;
    text-shadow: 0 2px 6px rgba(0,0,0,0.45);
  }
  .btn {
    display: flex; align-items: center; justify-content: center;
    background: var(--purple); color: var(--white); border-radius: 21px;
    font-size: 15px;
  }
  .hero-btn { left: 532px; top: 339px; width: 136px; height: 41px; }
  .hero-arrows { left: 572px; top: 574px; }

  /* Welcome */
  .welcome-title { top: 738px; font-size: 49px; color: var(--black); }
  .welcome-sub { top: 800px; font-size: 36px; color: var(--purple); }
  .welcome-text {
    left: 255px; top: 860px; width: 690px; text-align: center;
    font-size: 15.5px; line-height: 31px; color: var(--ink);
  }
  .welcome-btn { left: 532px; top: 1018px; width: 136px; height: 41px; }

  /* Services */
  .services-title { top: 1105px; font-size: 36px; color: var(--purple); }
  .tile { position: absolute; }
  .tile-feature {
    left: 112px; top: 1190px; width: 475px; height: 349px;
    background: linear-gradient(160deg, #2a231f 0%, #3a2c2a 40%, #1f2a18 75%, #2e3a1c 100%);
  }
  .feature-text { position: absolute; left: 0; width: 475px; text-align: center; color: var(--white); }
  .feature-name { top: 74px; font-family: "Lato", sans-serif; font-weight: 700; font-size: 16px; }
  .feature-meta { top: 102px; font-family: "Lora", serif; font-size: 19px; }
  .feature-desc {
    top: 142px; left: 40px; width: 395px; font-family: "Lato", sans-serif;
    font-size: 13.5px; line-height: 25.5px;
  }
  .feature-btn {
    left: 169px; top: 239px; width: 137px; height: 39px;
    font-family: "Lato", sans-serif; font-weight: 700; font-size: 15px; position: absolute;
  }
  .tile-herd { left: 611px; top: 1189px; width: 476px; height: 350px;
    background: linear-gradient(180deg, #3f78c8 0%, #9fbfe6 35%, #5a4330 55%, #4a7f2e 80%, #5c8d34 100%); }
  .tile-paddock { left: 109px; top: 1565px; width: 311px; height: 276px;
    background: linear-gradient(180deg, #9a9a9a 0%, #d8cbb0 22%, #3d4a2c 45%, #5f8a2a 70%, #6f9a2e 100%); }
  .tile-aerial { left: 443px; top: 1565px; width: 311px; height: 276px;
    background: linear-gradient(180deg, #5f86b8 0%, #4a6a3a 14%, #3f7a2e 40%, #5e9a34 100%); }
  .tile-farm { left: 775px; top: 1565px; width: 312px; height: 266px;
    background: linear-gradient(180deg, #8fa9c8 0%, #5f8440 14%, #4d7a30 50%, #3f6a28 100%); }

  /* Subscribe */
  .subscribe { left: 0; top: 1914px; width: 1200px; height: 267px; background: var(--purple-deep); }
  .subscribe-title { top: 1964px; font-family: "Lato", sans-serif; font-weight: 700; font-size: 26px; color: var(--white); }
  .subscribe-note { top: 2001px; font-family: "Lora", serif; font-size: 12px; color: var(--white); }
  .subscribe-input { left: 381px; top: 2045px; width: 300px; height: 41px; background: var(--white); }
  .subscribe-btn {
    left: 693px; top: 2045px; width: 128px; height: 41px; background: var(--black); color: var(--white);
    display: flex; align-items: center; justify-content: center; font-family: "Lora", serif; font-size: 15px;
  }

  /* Footer */
  .footer-badge {
    left: 559px; top: 2149px; width: 82px; height: 82px; border-radius: 50%; background: var(--white);
    display: flex; align-items: center; justify-content: center; text-align: center;
    color: var(--purple); font-size: 11px; line-height: 13px;
  }
  .footer-link { position: absolute; top: 2255px; font-size: 18px; color: var(--black); transform: translateX(-50%); white-space: nowrap; }
  .contact { position: absolute; top: 2314px; font-size: 13px; color: var(--black); white-space: nowrap; }
  .contact-icon { position: absolute; top: 2314px; }
  .copyright { top: 2359px; font-size: 13px; color: var(--black); }
</style>
</head>
<body>

  <section class="abs hero" role="img" aria-label="Photo of a paddock at sunset with timber fences, grazing horse and cloudy sky"></section>
  <div class="abs hero-tree"></div>

  <div class="abs brand">Marlow Vale Stud</div>

  <nav class="abs nav">
    <div class="abs nav-active"></div>
    <span class="nav-item" style="left:540px">HOME</span>
    <span class="nav-item" style="left:629px">ABOUT US</span>
    <span class="nav-item" style="left:730px">SERVICES</span>
    <span class="nav-item" style="left:847px">TESTIMONIALS</span>
    <span class="nav-item" style="left:945px">FAQ</span>
    <span class="nav-item" style="left:1037px">CONTACT US</span>
  </nav>

  <h1 class="abs center-x hero-title">MARLOW VALE STUD.</h1>
  <div class="abs btn hero-btn">READ MORE</div>

  <svg class="abs hero-arrows" width="56" height="28" viewBox="0 0 56 28" aria-hidden="true">
    <path d="M14 5 L6 14 L14 23" fill="none" stroke="#fff" stroke-width="4"/>
    <path d="M42 5 L50 14 L42 23" fill="none" stroke="#fff" stroke-width="4"/>
  </svg>

  <h2 class="abs center-x welcome-title">WELCOME TO</h2>
  <p class="abs center-x welcome-sub">Marlow Vale Stud</p>
  <p class="abs welcome-text">Lorem ipsum dolor sit amet, consectetur adipiscing elit, sed do eiusmod tempor incididunt ut labore et dolore magna aliqua. Ut enim ad minim veniam, quis nostrud exercitation ullamco laboris nisi ut aliquip ex ea commodo consequat. Duis aute irure dolor in reprehenderit in voluptate velit esse cillum dolore</p>
  <div class="abs btn welcome-btn">READ MORE</div>

  <h2 class="abs center-x services-title">Services</h2>

  <article class="tile tile-feature" role="img" aria-label="Photo of a racehorse and jockey on the track, darkened behind text">
    <p class="feature-text feature-name">FROSTED CROWN (USA)</p>
    <p class="feature-text feature-meta">Duration varies • Price varies</p>
    <p class="feature-text feature-desc">Frosted Crown (USA). Double dilute thoroughbred stallion, guaranteed palomino or buckskin. Available for live cover and for frozen/chilled semen later this season.</p>
    <div class="btn feature-btn">LEARN MORE</div>
  </article>
  <div class="tile tile-herd" role="img" aria-label="Photo of five young horses standing in a green paddock under blue sky"></div>
  <div class="tile tile-paddock" role="img" aria-label="Photo of two horses grazing in a paddock beneath cloudy sky"></div>
  <div class="tile tile-aerial" role="img" aria-label="Aerial photo of fenced green paddocks with shelters"></div>
  <div class="tile tile-farm" role="img" aria-label="Aerial photo of the farm buildings, dams and paddocks"></div>

  <section class="abs subscribe"></section>
  <h3 class="abs center-x subscribe-title">SUBSCRIBE</h3>
  <p class="abs center-x subscribe-note">Sign up with your email address to receive news and updates.</p>
  <div class="abs subscribe-input"></div>
  <div class="abs subscribe-btn">SIGN UP</div>

  <div class="abs footer-badge">Marlow<br>Vale Stud</div>

  <nav>
    <span class="footer-link" style="left:315px">Home</span>
    <span class="footer-link" style="left:417px">About Us</span>
    <span class="footer-link" style="left:529px">Services</span>
    <span class="footer-link" style="left:652px">Testimonials</span>
    <span class="footer-link" style="left:761px">FAQ</span>
    <span class="footer-link" style="left:864px">Contact Us</span>
  </nav>

  <svg class="contact-icon" style="left:296px" width="14" height="18" viewBox="0 0 14 18" aria-hidden="true">
    <path d="M7 0 C3 0 0 3 0 7 C0 11 7 18 7 18 C7 18 14 11 14 7 C14 3 11 0 7 0 Z" fill="#000"/>
    <circle cx="7" cy="7" r="2.6" fill="#fff"/>
  </svg>
  <span class="contact" style="left:323px">#123 Lorium ipsum,Dolor Amit.deo.</span>

  <svg class="contact-icon" style="left:582px" width="16" height="16" viewBox="0 0 16 16" aria-hidden="true">
    <path d="M3 0 L6 0 L7 4 L5 6 C6 8.5 7.5 10 10 11 L12 9 L16 10 L16 13 C16 15 15 16 13 16 C6 15 1 10 0 3 C0 1 1 0 3 0 Z" fill="#000"/>
  </svg>
  <span class="contact" style="left:616px">1-800 567 8906</span>

  <svg class="contact-icon" style="left:750px;top:2317px" width="16" height="12" viewBox="0 0 16 12" aria-hidden="true">
    <rect width="16" height="12" rx="1.5" fill="#000"/>
    <path d="M1 1.5 L8 7 L15 1.5" fill="none" stroke="#fff" stroke-width="1.4"/>
  </svg>
  <span class="contact" style="left:775px">info@sitename.com</span>

  <p class="abs center-x copyright">© 2019 &nbsp;|&nbsp; www.companyname.com</p>

</body>
</html>
```